Harborline Auto LLC

Car Dealer Customer Service
Address: 2874 Cresthaven Road, Shelbyville, TN 37162
web: www.harborlineautoxq.net
email: harborlineautoxq@mailnest.example
Phone: (931) 555-0148
Phone: (629) 555-0173

```html
<!DOCTYPE html>
<html lang="en">
<head>
<meta charset="utf-8">
<title>Harborline Auto LLC – Business Card</title>
<link href="https://fonts.googleapis.com/css2?family=Montserrat:wght@400;500;700;800&display=swap" rel="stylesheet">
<style>
  :root {
    --backdrop: #3b3b3b;
    --card: #1a1a1a;
    --card-back: #151515;
    --brand-blue: #1f86c9;
    --edge-blue: #1c8fe0;
    --accent-gold: #f3b23a;
    --text-light: #f2f2f2;
    --emboss: #2b2b2b;
  }
  * { margin: 0; padding: 0; box-sizing: border-box; }
  html, body { width: 1200px; height: 801px; overflow: hidden; }
  body {
    background: var(--backdrop);
    font-family: "Montserrat", Arial, sans-serif;
    display: flex;
    align-items: center;
    justify-content: center;
    gap: 44px;
  }
  .card {
    position: relative;
    width: 520px;
    height: 297px;
    background: var(--card);
    border-bottom: 3px solid var(--edge-blue);
    box-shadow: 0 10px 24px rgba(0,0,0,.35);
  }
  .card--back { background: var(--card-back); }

  .brand {
    position: absolute;
    top: 58px;
    left: 0; right: 0;
    display: flex;
    align-items: center;
    justify-content: center;
    gap: 12px;
  }
  .brand__dot {
    width: 34px; height: 34px;
    border-radius: 50%;
    background: var(--brand-blue);
  }
  .brand__name {
    color: var(--brand-blue);
    font-weight: 800;
    font-size: 30px;
    letter-spacing: .5px;
    text-transform: uppercase;
  }

  .tagline {
    position: absolute;
    top: 128px;
    left: 24px; right: 24px;
    display: flex;
    align-items: center;
    gap: 10px;
  }
  .tagline__rule { flex: 1; height: 1.5px; background: var(--accent-gold); }
  .tagline__text {
    color: var(--brand-blue);
    font-weight: 700;
    font-size: 17px;
    text-transform: uppercase;
    white-space: nowrap;
  }

  .contact {
    position: absolute;
    bottom: 28px;
    left: 28px;
    list-style: none;
    color: var(--text-light);
    font-size: 13.5px;
    line-height: 21px;
  }
  .contact li { display: flex; align-items: center; gap: 8px; }
  .contact svg { width: 12px; height: 12px; fill: var(--accent-gold); flex: none; }

  .location {
    position: absolute;
    bottom: 28px;
    right: 28px;
    text-align: right;
    color: var(--text-light);
    font-size: 13.5px;
    line-height: 21px;
  }
  .location__web { color: var(--accent-gold); }

  .back-mark {
    position: absolute;
    inset: 0;
    display: flex;
    align-items: center;
    justify-content: center;
    gap: 14px;
  }
  .back-mark__dot { width: 70px; height: 70px; border-radius: 50%; background: var(--emboss); }
  .back-mark__name {
    color: var(--emboss);
    font-weight: 800;
    font-size: 30px;
    text-transform: uppercase;
  }
</style>
</head>
<body>
  <section class="card card--front">
    <div class="brand">
      <span class="brand__dot"></span>
      <span class="brand__name">Harborline Auto</span>
    </div>

    <div class="tagline">
      <span class="tagline__rule"></span>
      <span class="tagline__text">Car Dealer Customer Service</span>
      <span class="tagline__rule"></span>
    </div>

    <ul class="contact">
      <li>
        <svg viewBox="0 0 24 24" aria-hidden="true"><path d="M6.6 10.8a15.1 15.1 0 0 0 6.6 6.6l2.2-2.2c.3-.3.7-.4 1-.2 1.1.4 2.3.6 3.6.6.6 0 1 .4 1 1V20c0 .6-.4 1-1 1A17 17 0 0 1 3 4c0-.6.4-1 1-1h3.5c.6 0 1 .4 1 1 0 1.3.2 2.5.6 3.6.1.3 0 .7-.2 1z"/></svg>
        (931) 555-0148
      </li>
      <li>
        <svg viewBox="0 0 24 24" aria-hidden="true"><path d="M6.6 10.8a15.1 15.1 0 0 0 6.6 6.6l2.2-2.2c.3-.3.7-.4 1-.2 1.1.4 2.3.6 3.6.6.6 0 1 .4 1 1V20c0 .6-.4 1-1 1A17 17 0 0 1 3 4c0-.6.4-1 1-1h3.5c.6 0 1 .4 1 1 0 1.3.2 2.5.6 3.6.1.3 0 .7-.2 1z"/></svg>
        (629) 555-0173
      </li>
      <li>
        <svg viewBox="0 0 24 24" aria-hidden="true"><path d="M2 5h20v14H2z M2 5l10 8 10-8" /></svg>
        harborlineautoxq@mailnest.example
      </li>
    </ul>

    <address class="location" style="font-style:normal">
      2874 Cresthaven Road<br>
      Shelbyville, TN 37162<br>
      <span class="location__web">www.harborlineautoxq.net</span>
    </address>
  </section>

  <section class="card card--back">
    <div class="back-mark">
      <span class="back-mark__dot"></span>
      <span class="back-mark__name">Harborline Auto</span>
    </div>
  </section>
</body>
</html>
```